Ledgerline Code Works business card design.

We are a software development company that develop Software for finance companies and related industries.

We need a 2 sided business card designed. We have a new logo already designed (see attached eps and ai) We are after a clean simple corporate look. One side with just our logo, and the second side with our details.

Greg Halvorsen
Managing Director

Suite 5 Level 8, 147 Marlow Street Sydney NSW 2000

Direct: +61 2 9387 4625
Mobile: +61 4 1736 8490
Email: gregh@lcw.net.au
Web: www.lcw.net.au

I have included 2 logo files an .ai and .eps. I noticed that the lines either side of the partners looks a bit jaggered and needs to be made sharper.

I would like to introduce a little colour somewhere rather than having it all black and white. But not over the top, keeping with a simple clean corporate look. Perhaps a light blue on some of the text?

If you have other ideas would be pleased to review

Regards

Greg H.

```html
<!DOCTYPE html>
<html lang="en">
<head>
<meta charset="utf-8">
<title>Ledgerline Code Works — Business Card</title>
<link rel="stylesheet" href="https://fonts.googleapis.com/css2?family=Open+Sans:wght@400;600;700&display=swap">
<style>
  :root {
    --backdrop: #3b3b3d;
    --card: #1d1b1b;
    --card-edge: #141212;
    --ink-light: #f2f2f2;
    --ink-soft: #d9d9d9;
    --accent: #5ab6e6;
  }
  * { box-sizing: border-box; margin: 0; padding: 0; }
  html, body {
    width: 1200px;
    height: 768px;
    overflow: hidden;
    background: var(--backdrop);
    font-family: "Open Sans", Arial, sans-serif;
  }
  .stage {
    position: relative;
    width: 1200px;
    height: 768px;
    display: flex;
    align-items: center;
    justify-content: center;
    gap: 60px;
  }
  .card {
    position: relative;
    width: 525px;
    height: 300px;
    background: var(--card);
    border-radius: 4px;
    box-shadow: 0 14px 30px rgba(0,0,0,0.45), 0 0 0 1px var(--card-edge);
    overflow: hidden;
  }

  /* Front side */
  .card--front {
    display: flex;
    align-items: center;
    justify-content: center;
  }
  .front-brand {
    display: flex;
    align-items: center;
    gap: 14px;
  }
  .front-brand__mark {
    width: 14px;
    height: 14px;
    background: var(--ink-light);
  }
  .front-brand__name {
    color: var(--ink-light);
    font-weight: 700;
    font-size: 25px;
    letter-spacing: 0.5px;
  }

  /* Back side */
  .card--back {
    display: flex;
    align-items: center;
    padding: 0 36px 0 38px;
    gap: 30px;
  }
  .back-brand {
    width: 170px;
    display: flex;
    align-items: center;
    gap: 10px;
  }
  .back-brand__mark {
    flex: none;
    width: 12px;
    height: 12px;
    background: var(--accent);
  }
  .back-brand__name {
    color: var(--accent);
    font-weight: 700;
    font-size: 21px;
    line-height: 1.15;
  }
  .details {
    color: var(--ink-soft);
    font-size: 13px;
    line-height: 1.45;
  }
  .details__name {
    color: var(--accent);
    font-weight: 700;
    font-size: 15px;
    line-height: 1.2;
  }
  .details__role {
    font-size: 11.5px;
    margin-bottom: 16px;
  }
  .details__address { margin-bottom: 14px; }
  .contact-list { list-style: none; }
  .contact-list li {
    display: flex;
    align-items: center;
    gap: 9px;
  }
  .contact-list svg {
    width: 11px;
    height: 11px;
    flex: none;
    fill: var(--accent);
  }
  .web-accent { color: var(--accent); }
</style>
</head>
<body>
<main class="stage">

  <section class="card card--front" aria-label="Card front">
    <div class="front-brand">
      <span class="front-brand__mark"></span>
      <span class="front-brand__name">Ledgerline Code Works</span>
    </div>
  </section>

  <section class="card card--back" aria-label="Card back">
    <div class="back-brand">
      <span class="back-brand__mark"></span>
      <span class="back-brand__name">Ledgerline Code Works</span>
    </div>

    <div class="details">
      <p class="details__name">Greg Halvorsen</p>
      <p class="details__role">Managing Director</p>
      <p class="details__address">Suite 5 Level 8, 147 Marlow Street<br>Sydney NSW 2000</p>
      <ul class="contact-list">
        <li>
          <svg viewBox="0 0 12 12" aria-hidden="true"><path d="M1 4c0-2 2-3 5-3s5 1 5 3l-2 1-1-2H4L3 5 1 4zm2 2h6l1 5H2l1-5zm3 1.3a1.4 1.4 0 1 0 0 2.8 1.4 1.4 0 0 0 0-2.8z"/></svg>
          <span>+61 2 9387 4625</span>
        </li>
        <li>
          <svg viewBox="0 0 12 12" aria-hidden="true"><path d="M3 0h6a1 1 0 0 1 1 1v10a1 1 0 0 1-1 1H3a1 1 0 0 1-1-1V1a1 1 0 0 1 1-1zm0 1.5v8h6v-8H3zm3 8.7a.6.6 0 1 0 0 1.2.6.6 0 0 0 0-1.2z"/></svg>
          <span>+61 4 1736 8490</span>
        </li>
        <li>
          <svg viewBox="0 0 12 12" aria-hidden="true"><path d="M0 2h12v8H0V2zm1 1v.4l5 3.4 5-3.4V3H1zm0 1.6V9h10V4.6L6 8 1 4.6z"/></svg>
          <span>gregh@lcw.net.au</span>
        </li>
        <li>
          <svg viewBox="0 0 12 12" aria-hidden="true"><path d="M6 0a6 6 0 1 0 0 12A6 6 0 0 0 6 0zm4.4 5.3H8.6A9 9 0 0 0 7.7 1.4a4.6 4.6 0 0 1 2.7 3.9zM6 1.3c.6.8 1.2 2.2 1.3 4H4.7C4.8 3.5 5.4 2.1 6 1.3zM4.3 1.4a9 9 0 0 0-.9 3.9H1.6a4.6 4.6 0 0 1 2.7-3.9zM1.6 6.7h1.8a9 9 0 0 0 .9 3.9 4.6 4.6 0 0 1-2.7-3.9zM6 10.7c-.6-.8-1.2-2.2-1.3-4h2.6c-.1 1.8-.7 3.2-1.3 4zm1.7-.1a9 9 0 0 0 .9-3.9h1.8a4.6 4.6 0 0 1-2.7 3.9z"/></svg>
          <span>www.<span class="web-accent">lcw</span>.net.au</span>
        </li>
      </ul>
    </div>
  </section>

</main>
</body>
</html>
```